Brightwave Reach - Business Card

We need a business card for a Social Media Marketing company that specializes in online marketing for small businesses in Canada using common Social Media platforms such as Pixlora, Chatterly, Blinkpost & Quibber.

I have uploaded a copy of our logo which I would like utilized in the business card. We would like the business card to be modern yet classy design.

Our website is www.brightwavereach.ca

Industry/Entity Type

Marketing

Contact Information for Business Card

Email: info@brightwavereach.ca
Website: www.brightwavereach.ca
Telephone: 604-555-0193

Colors

Designer to choose colors to be used in the design.

Requirements
Must have
• Social Media icons on reverse
• Please add some designs with color.

```html
<!DOCTYPE html>
<html lang="en">
<head>
<meta charset="UTF-8">
<title>Brightwave Reach – Business Card</title>
<link href="https://fonts.googleapis.com/css2?family=Roboto:wght@400;700&display=swap" rel="stylesheet">
<style>
  :root {
    --backdrop: #e6e4e1;
    --card: #3b3f42;
    --ink: #ffffff;
    --ink-soft: #e9eaea;
    --leaf-tone: #d9d9d6;
  }
  * { box-sizing: border-box; margin: 0; padding: 0; }
  html, body {
    width: 1200px; height: 1200px; overflow: hidden;
    background: var(--backdrop);
    font-family: "Roboto", Arial, sans-serif;
    color: var(--ink);
  }
  .canvas { position: relative; width: 1200px; height: 1200px; }
  .card {
    position: absolute; left: 213px; width: 775px; height: 445px;
    background: var(--card);
    box-shadow: 0 6px 18px rgba(0,0,0,0.25);
    overflow: hidden;
  }
  .card--front { top: 150px; }
  .card--back { top: 635px; }

  .brand-name {
    font-weight: 700; text-transform: uppercase; line-height: 1;
    color: var(--ink); text-align: center; letter-spacing: 0.5px;
  }
  .card--front .brand-name {
    position: absolute; left: 38px; top: 62px; width: 240px; font-size: 38px;
  }
  .card--front .brand-name span { display: block; }
  .card--front .brand-name span + span { margin-top: 6px; }

  .holder { position: absolute; left: 44px; top: 224px; }
  .holder-name { font-size: 27px; font-weight: 400; }
  .holder-role { font-size: 17px; margin-top: 6px; color: var(--ink-soft); }

  .contact-list {
    position: absolute; left: 44px; top: 326px; list-style: none;
    font-size: 17px; color: var(--ink-soft);
  }
  .contact-list li { display: flex; align-items: center; height: 27px; }
  .contact-list svg { width: 15px; height: 15px; margin-right: 7px; flex: none; }

  .leaf-art {
    position: absolute; left: 565px; top: 185px; width: 200px; height: 260px;
    background: radial-gradient(ellipse at 50% 40%, var(--leaf-tone) 0%, rgba(217,217,214,0.75) 55%, rgba(217,217,214,0) 72%);
  }

  .card--back .brand-name {
    position: absolute; left: 0; right: 0; top: 150px; font-size: 44px;
  }
  .card--back .brand-name span { display: block; }
  .card--back .brand-name span + span { margin-top: 8px; }

  .social-bar {
    position: absolute; left: 0; right: 0; top: 384px;
    display: flex; align-items: center; gap: 14px;
  }
  .social-bar .rule { flex: 1; height: 2px; background: var(--ink-soft); }
  .social-list { display: flex; gap: 12px; list-style: none; font-size: 13px; font-weight: 400; }
</style>
</head>
<body>
<main class="canvas">
  <section class="card card--front">
    <div class="brand-name"><span>Brightwave</span><span>Reach</span></div>

    <div class="holder">
      <p class="holder-name">Marcus Ellery</p>
      <p class="holder-role">President &amp; CEO</p>
    </div>

    <ul class="contact-list">
      <li>
        <svg viewBox="0 0 16 16" fill="none" stroke="currentColor" stroke-width="1.3"><path d="M3 1.5l2.5 0 1.2 3-1.6 1.2a8 8 0 0 0 5.2 5.2l1.2-1.6 3 1.2v2.5a1.5 1.5 0 0 1-1.6 1.5A12.5 12.5 0 0 1 1.5 3.1 1.5 1.5 0 0 1 3 1.5z"/></svg>
        604-555-0193
      </li>
      <li>
        <svg viewBox="0 0 16 16" fill="none" stroke="currentColor" stroke-width="1.3"><rect x="1.5" y="3.5" width="13" height="9"/><path d="M1.5 3.5l6.5 5 6.5-5"/></svg>
        info@brightwavereach.ca
      </li>
      <li>
        <svg viewBox="0 0 16 16" fill="none" stroke="currentColor" stroke-width="1.3"><circle cx="8" cy="8" r="6.5"/><ellipse cx="8" cy="8" rx="3" ry="6.5"/><path d="M1.5 8h13"/></svg>
        www.brightwavereach.ca
      </li>
    </ul>

    <div class="leaf-art" role="img" aria-label="Large distressed white maple leaf decoration"></div>
  </section>

  <section class="card card--back">
    <div class="brand-name"><span>Brightwave</span><span>Reach</span></div>
    <div class="social-bar">
      <span class="rule"></span>
      <ul class="social-list">
        <li>Chatterly</li>
        <li>Linkwise</li>
        <li>Quibber</li>
        <li>Callora</li>
      </ul>
      <span class="rule"></span>
    </div>
  </section>
</main>
</body>
</html>
```